Business Card Re-Design/Update

We'd like to update out business cards. I've included our current "Style guide" which has the colour scheme of the organisation in it. I've also included the branding files with logos etc in them.

I've also included a copy of one of our existing cards so that you can see how ugly/dated they look. I'd like a fresh modern corporate look.

Target Market(s)

These are for our clients, potential clients, industry contacts - like all business cards

Contact Information for Business Card

Name
Position
Company Address - Level 1, 47 Fernby Street, Carlow Qld 4072
Direct Phone
mobile
Email
Website -www.korvalit.com.au
Logo

Colors

Designer to choose colors to be used in the design.

Requirements
Must have
• Main Logo
• Cards will need to be editable to be able to personalize them for each new employee.
Nice to have
• The MapOut, ShipWell, KeepSteady would be okay to have if they can be sensibly and professionally added to the look without detracting from the main imagery.
• Maybe they could go on the back of the card? will leave this to your creative discretion as to whether/where they fit.
Should not have
• Should not have decorative or script fonts

```html
<!DOCTYPE html>
<html lang="en">
<head>
<meta charset="utf-8">
<title>korvalIT business card</title>
<link rel="stylesheet" href="https://fonts.googleapis.com/css2?family=Work+Sans:wght@400;500;600&display=swap">
<style>
  :root {
    --page: #e9e4dc;
    --card: #f6f5f2;
    --card-edge: #dcd8d1;
    --brand-blue: #2a86b4;
    --ink: #4b4b4b;
  }
  * { margin: 0; padding: 0; box-sizing: border-box; }
  html, body {
    width: 1200px;
    height: 1047px;
    overflow: hidden;
    background: var(--page);
    font-family: "Work Sans", Arial, sans-serif;
  }
  .card {
    position: absolute;
    left: 151px;
    top: 291px;
    width: 944px;
    height: 513px;
    background: var(--card);
    border: 1px solid var(--card-edge);
    border-radius: 22px;
    box-shadow: 0 10px 30px rgba(0,0,0,0.08);
  }
  .brand {
    position: absolute;
    left: 54px;
    top: 54px;
    display: flex;
    align-items: center;
    gap: 14px;
  }
  .brand-square {
    width: 34px;
    height: 34px;
    background: var(--brand-blue);
  }
  .brand-name {
    font-size: 48px;
    font-weight: 500;
    color: var(--brand-blue);
    letter-spacing: 0.5px;
    line-height: 1;
  }
  .person {
    position: absolute;
    left: 54px;
    top: 142px;
  }
  .person-name {
    font-size: 38px;
    font-weight: 600;
    color: var(--brand-blue);
    letter-spacing: 0.5px;
    line-height: 1.1;
  }
  .person-role {
    font-size: 22px;
    color: var(--ink);
    letter-spacing: 0.6px;
    margin-top: 2px;
  }
  .address {
    position: absolute;
    left: 54px;
    top: 228px;
    font-size: 21px;
    line-height: 28px;
    color: var(--ink);
    letter-spacing: 0.6px;
  }
  .contacts {
    position: absolute;
    left: 54px;
    top: 300px;
    list-style: none;
  }
  .contacts li {
    display: flex;
    align-items: center;
    height: 28.5px;
    font-size: 21px;
    color: var(--ink);
    letter-spacing: 0.6px;
  }
  .contacts svg {
    width: 14px;
    height: 14px;
    margin-right: 14px;
    fill: var(--brand-blue);
    flex: none;
  }
  .web-accent { color: var(--brand-blue); }
  .brand-feature {
    position: absolute;
    left: 547px;
    top: 122px;
    width: 270px;
    height: 270px;
    background: var(--brand-blue);
  }
</style>
</head>
<body>
  <main class="card">
    <div class="brand">
      <span class="brand-square"></span>
      <span class="brand-name">korvalIT</span>
    </div>

    <div class="person">
      <h1 class="person-name">DANA WHITLOCK</h1>
      <p class="person-role">Business Development Manager</p>
    </div>

    <p class="address">Level 1, 47 Fernby Street,<br>Carlow Qld 4072</p>

    <ul class="contacts">
      <li>
        <svg viewBox="0 0 14 14" aria-hidden="true"><path d="M3 0h8a1 1 0 0 1 1 1v12a1 1 0 0 1-1 1H3a1 1 0 0 1-1-1V1a1 1 0 0 1 1-1zm1 2v8h6V2zm3 9a1 1 0 1 0 0 2 1 1 0 0 0 0-2z"/></svg>
        +61 (0)400 555 018
      </li>
      <li>
        <svg viewBox="0 0 14 14" aria-hidden="true"><path d="M1 4c2-3 10-3 12 0l-1 2-3-1V4H5v1L2 6zM3 8h8l1 5H2z"/></svg>
        +61 (0)7 5550 1426
      </li>
      <li>
        <svg viewBox="0 0 14 14" aria-hidden="true"><path d="M3 0l3 3-2 2c1 2 3 4 5 5l2-2 3 3-2 3C6 13 1 8 0 3z"/></svg>
        +61 (0)7 5550 1400
      </li>
      <li>
        <svg viewBox="0 0 14 14" aria-hidden="true"><path d="M4 0h6v4H4zM1 5h12v6h-2V9H3v2H1zm3 5h6v4H4z"/></svg>
        +61 (0)7 5550 1409
      </li>
      <li>
        <svg viewBox="0 0 14 14" aria-hidden="true"><path d="M0 2h14v10H0zm1.5 1.5v.3L7 8l5.5-4.2v-.3zm0 2.2V10.5h11V5.7L7 9.8z"/></svg>
        dwhitlock@korvalit.com.au
      </li>
      <li>
        <svg viewBox="0 0 14 14" aria-hidden="true"><path d="M7 0a7 7 0 1 0 0 14A7 7 0 0 0 7 0zm-1 1.6C5 3 4.5 4.8 4.4 6.3H1.6A5.5 5.5 0 0 1 6 1.6zm2 0a5.5 5.5 0 0 1 4.4 4.7H9.6C9.5 4.8 9 3 8 1.6zM5.9 6.3C6 4.9 6.4 3.5 7 2.4c.6 1.1 1 2.5 1.1 3.9zM1.6 7.7h2.8c.1 1.5.6 3.3 1.6 4.7a5.5 5.5 0 0 1-4.4-4.7zm4.3 0h2.2C8 9.1 7.6 10.5 7 11.6 6.4 10.5 6 9.1 5.9 7.7zm3.7 0h2.8A5.5 5.5 0 0 1 8 12.4c1-1.4 1.5-3.2 1.6-4.7z"/></svg>
        www.<span class="web-accent">korvalit</span>.com.au
      </li>
    </ul>

    <div class="brand-feature" role="img" aria-label="Large korvalIT brand mark area"></div>
  </main>
</body>
</html>
```